KBT Business Cards

We require business cards for our business. We would like a matte black back to the card, with our logo centred in the middle. The front side of the card is open to design.

Target Market(s)

Clients looking for legal services (professional)

Industry/Entity Type

Legal

Contact Information for Business Card

Doran Kelbrath
Partner
Mobile: 0461 738 524
Email: doran@kbtlaw.co
Website: www.kbtlaw.co
Level 3, 118 Wendmore Street
Sydney NSW 2000

Font styles to use
Other font styles liked:
• Avenir

Colors
f04a50
ffffff
1b1b1b

Requirements
Must have
• Black back with logo included in the centre of the card.
• Our font is Avenir.

```html
<!DOCTYPE html>
<html lang="en">
<head>
<meta charset="utf-8">
<title>KBT Business Cards</title>
<link href="https://fonts.googleapis.com/css2?family=Lato:wght@400&family=Roboto:wght@400;500;700&display=swap" rel="stylesheet">
<style>
  :root {
    --stage: #9e9e9e;
    --paper: #ffffff;
    --ink: #1b1b1b;
    --accent: #c0183c;
    --accent-bright: #f04a50;
    --matte: #231f20;
    --back-text: #e8e8e8;
    --shadow: rgba(0, 0, 0, 0.45);
  }
  * { margin: 0; padding: 0; box-sizing: border-box; }
  html, body { width: 1200px; height: 900px; overflow: hidden; }
  body { background: var(--stage); position: relative; font-family: "Lato", sans-serif; }

  .card { position: absolute; top: 200px; width: 310px; height: 502px; box-shadow: 3px 4px 6px var(--shadow); }
  .card-front { left: 253px; background: var(--paper); border-radius: 60px 0 60px 0; }
  .card-back  { left: 627px; background: var(--matte); border-radius: 0 60px 0 60px; }

  .brand-square { position: absolute; left: 66px; top: 148px; width: 40px; height: 40px; background: var(--accent); }
  .brand-name {
    position: absolute; left: 152px; top: 132px;
    font-family: "Roboto", sans-serif; font-weight: 500; font-size: 21px;
    line-height: 24px; color: var(--ink); text-transform: uppercase;
  }

  .person { position: absolute; left: 33px; top: 321px; }
  .person-name {
    font-family: "Roboto", sans-serif; font-weight: 700; font-size: 17px;
    color: var(--accent); text-transform: uppercase; line-height: 20px;
  }
  .person-role { font-size: 13.5px; color: var(--ink); line-height: 17px; }

  .contacts { position: absolute; left: 33px; top: 367px; list-style: none; }
  .contacts li { display: flex; align-items: center; gap: 5px; font-size: 14px; line-height: 18.5px; color: var(--ink); }
  .contacts svg { width: 11px; height: 11px; fill: var(--accent); flex: none; }

  .address { position: absolute; left: 33px; top: 432px; font-size: 14px; line-height: 19px; color: var(--ink); font-style: normal; }

  .back-mark { position: absolute; left: 127px; top: 223px; width: 56px; height: 56px; background: var(--accent-bright); }

  .back-web {
    position: absolute; left: 0; right: 0; top: 438px; text-align: center;
    font-family: "Roboto", sans-serif; font-size: 15px; letter-spacing: 1.6px; color: var(--back-text);
  }
</style>
</head>
<body>
  <section class="card card-front" aria-label="Card front">
    <span class="brand-square"></span>
    <div class="brand-name">Kelbrath<br>Brant<br>Tarrow</div>

    <div class="person">
      <div class="person-name">Doran Kelbrath</div>
      <div class="person-role">Partner</div>
    </div>

    <ul class="contacts">
      <li>
        <svg viewBox="0 0 12 12" aria-hidden="true"><path d="M1 4.5C1 3 2.5 2 6 2s5 1 5 2.5L9 5.2 8.3 4H3.7L3 5.2zM3 6h6l1.5 4.5h-9zM6 7a1.3 1.3 0 1 0 0 2.6A1.3 1.3 0 0 0 6 7z"/></svg>
        0461 738 524
      </li>
      <li>
        <svg viewBox="0 0 12 12" aria-hidden="true"><path d="M1 2.5h10v7H1zM1.8 3.3 6 6.6l4.2-3.3v.9L6 7.5 1.8 4.2z" fill-rule="evenodd"/></svg>
        doran@kbtlaw.co
      </li>
      <li>
        <svg viewBox="0 0 12 12" aria-hidden="true"><path d="M6 1a5 5 0 1 0 0 10A5 5 0 0 0 6 1zm-1 2.2 2 .8-.6 1.6 1.8 1-1 2.2-1.6-.8.2-1.6L4 5.6z"/></svg>
        www.kbtlaw.co
      </li>
    </ul>

    <address class="address">Level 3, 118 Wendmore<br>Street, Sydney NSW 2000</address>
  </section>

  <section class="card card-back" aria-label="Card back">
    <span class="back-mark" role="img" aria-label="KBT logo mark"></span>
    <div class="back-web">www.kbtlaw.co</div>
  </section>
</body>
</html>
```